Figure for presentation on a hybrid research project

We need a figure that shows a series of 6 technical projects feeding into 3 multidisciplinary hybrid projects.
The concept is a ring of 6 technical projects, which could look like a 6 colour swirl (see
https://en.plorvanex.org/wiki/Vector_graphics for an example of a 4 colour swirl.)
The 3 hybrid projects sit in the centre because they rely on input from many of the surrounding technical projects.
I've drawn a rough version in Powerpoint - see attached file uploaded. Note, in my example I couldn't draw the swirling outer ring and the colour selection is poor. The acronym for the overall Centre using the figure is VexORDA, so we will have a mint leaf and turquoise green in the logo, plus also nerves, since we will be researching neural interconnections.
We ABSOLUTELY NEED the final form of the figure to include vector graphics formats (including a form that can be edited in Photoshop) because we may need to change the title of the technical projects or of the hybrid projects at short notice ourselves.

Target Market(s)

Academic: eminent scientists and engineers

Industry/Entity Type

Technical

Font styles to use
Sans Serif

Colors
04a990

Requirements
Must have
• The projects around the ring with all project titles legible; the final figure will be reduced to no more than 8cm x 8cm in the proposal (probably less).
• Only one colour selected, because we have included that colour in the logo that we are having designed. Otherwise, a colour series around the ring that is pleasant, and another compatible colour series for the inter 3 projects.
• We ABSOLUTELY NEED the final form of the figure to include vector graphics formats (including a form that can be edited in Photoshop) because we may need to change the title of the technical projects or of the hybrid projects at short notice ourselves.
Nice to have
• See the figure we uploaded; that's the essence
• HOWEVER VIP: two of the titles around the outer ring have changed slightly.
• Computational Modelling is now Neuronal Modelling and
• Signal Processing is now Non-Invasive Interfaces (note that I've now changed the titles on the uploaded figure)

```html
<!DOCTYPE html>
<html lang="en">
<head>
<meta charset="utf-8">
<title>VexORDA – Research Programme Figure</title>
<link rel="stylesheet" href="https://fonts.googleapis.com/css2?family=Montserrat:wght@700;800&display=swap">
<style>
  :root {
    --teal: #04a990;
    --teal-light: #05a88f;
    --teal-soft: #06a088;
    --teal-mid: #07947c;
    --teal-deep: #077b64;
    --white: #ffffff;
    --ink-font: "Montserrat", Arial, sans-serif;
  }
  html, body {
    margin: 0;
    padding: 0;
    width: 1200px;
    height: 999px;
    overflow: hidden;
    background: var(--white);
  }
  .programme-figure {
    display: block;
    width: 1200px;
    height: 999px;
  }
  .petal--light { fill: var(--teal-light); }
  .petal--soft { fill: var(--teal-soft); }
  .petal--mid { fill: var(--teal-mid); }
  .petal--deep { fill: var(--teal-deep); }
  .project-label {
    font-family: var(--ink-font);
    font-weight: 700;
    font-size: 21px;
    fill: var(--white);
    letter-spacing: 0.2px;
  }
  .hub-disc { fill: var(--white); stroke: var(--teal); stroke-width: 6; }
  .hub-halo { fill: none; stroke: var(--white); stroke-width: 6; }
  .cycle-divider { fill: none; stroke: var(--teal); stroke-width: 3; stroke-linejoin: miter; }
  .cycle-label {
    font-family: var(--ink-font);
    font-weight: 800;
    font-size: 36px;
    fill: var(--teal);
    letter-spacing: 1.5px;
  }
  .centre-disc { fill: var(--teal); }
  .centre-ring { fill: none; stroke: var(--white); stroke-width: 3; }
  .centre-name {
    font-family: var(--ink-font);
    font-weight: 800;
    font-size: 32px;
    fill: var(--white);
  }
</style>
</head>
<body>
<svg class="programme-figure" viewBox="0 0 1134 944" xmlns="http://www.w3.org/2000/svg" role="img" aria-label="VexORDA programme: six technical projects swirling around three hybrid projects – Act, Connect, Perceive">
  <defs>
    <!-- label guides centred on angle 0; clockwise reads with tops outward, counter-clockwise with tops inward -->
    <path id="arc-outer-cw" d="M40.28,-228.48 A232,232 0 0,1 40.28,228.48"/>
    <path id="arc-outer-ccw" d="M43.41,246.20 A250,250 0 0,0 43.41,-246.20"/>
    <path id="arc-cycle-cw" d="M26.05,-147.72 A150,150 0 0,1 26.05,147.72"/>
    <path id="arc-cycle-ccw" d="M30.21,171.36 A174,174 0 0,0 30.21,-171.36"/>

    <!-- each petal is cut by the petal resting on top of it -->
    <mask id="cut-living" maskUnits="userSpaceOnUse" x="0" y="0" width="1134" height="944">
      <rect width="1134" height="944" fill="#fff"/>
      <circle cx="485.3" cy="528.9" r="275" fill="#000"/>
    </mask>
    <mask id="cut-gene" maskUnits="userSpaceOnUse" x="0" y="0" width="1134" height="944">
      <rect width="1134" height="944" fill="#fff"/>
      <circle cx="469.6" cy="430.2" r="275" fill="#000"/>
    </mask>
    <mask id="cut-electro" maskUnits="userSpaceOnUse" x="0" y="0" width="1134" height="944">
      <rect width="1134" height="944" fill="#fff"/>
      <circle cx="547.4" cy="367.2" r="275" fill="#000"/>
    </mask>
    <mask id="cut-optrode" maskUnits="userSpaceOnUse" x="0" y="0" width="1134" height="944">
      <rect width="1134" height="944" fill="#fff"/>
      <circle cx="640.7" cy="403.1" r="275" fill="#000"/>
    </mask>
    <mask id="cut-neuronal" maskUnits="userSpaceOnUse" x="0" y="0" width="1134" height="944">
      <rect width="1134" height="944" fill="#fff"/>
      <circle cx="656.4" cy="501.8" r="275" fill="#000"/>
    </mask>
    <mask id="cut-noninvasive" maskUnits="userSpaceOnUse" x="0" y="0" width="1134" height="944">
      <rect width="1134" height="944" fill="#fff"/>
      <circle cx="578.6" cy="564.8" r="275" fill="#000"/>
    </mask>
  </defs>

  <!-- outer swirl of technical projects -->
  <g class="technical-ring">
    <circle class="petal petal--deep" cx="469.6" cy="430.2" r="270" mask="url(#cut-living)"/>
    <circle class="petal petal--light" cx="547.4" cy="367.2" r="270" mask="url(#cut-gene)"/>
    <circle class="petal petal--deep" cx="640.7" cy="403.1" r="270" mask="url(#cut-electro)"/>
    <circle class="petal petal--mid" cx="656.4" cy="501.8" r="270" mask="url(#cut-optrode)"/>
    <circle class="petal petal--deep" cx="578.6" cy="564.8" r="270" mask="url(#cut-neuronal)"/>
    <circle class="petal petal--soft" cx="485.3" cy="528.9" r="270" mask="url(#cut-noninvasive)"/>
  </g>

  <g class="technical-labels">
    <g transform="translate(469.6 430.2) rotate(250)">
      <text class="project-label"><textPath href="#arc-outer-cw" startOffset="50%" text-anchor="middle">Living Electrodes</textPath></text>
    </g>
    <g transform="translate(547.4 367.2) rotate(308)">
      <text class="project-label"><textPath href="#arc-outer-cw" startOffset="50%" text-anchor="middle">Gene Regulated Interfaces</textPath></text>
    </g>
    <g transform="translate(640.7 403.1) rotate(10)">
      <text class="project-label"><textPath href="#arc-outer-ccw" startOffset="50%" text-anchor="middle">Electro-modulated Interfaces</textPath></text>
    </g>
    <g transform="translate(656.4 501.8) rotate(70)">
      <text class="project-label"><textPath href="#arc-outer-ccw" startOffset="50%" text-anchor="middle">Optrode Interfaces</textPath></text>
    </g>
    <g transform="translate(578.6 564.8) rotate(130)">
      <text class="project-label"><textPath href="#arc-outer-ccw" startOffset="50%" text-anchor="middle">Neuronal  Modelling</textPath></text>
    </g>
    <g transform="translate(485.3 528.9) rotate(190)">
      <text class="project-label"><textPath href="#arc-outer-cw" startOffset="50%" text-anchor="middle">Non-invasive Interfaces</textPath></text>
    </g>
  </g>

  <!-- hub with three hybrid projects -->
  <g class="hybrid-hub" transform="translate(563 467)">
    <circle class="hub-halo" r="214"/>
    <circle class="hub-disc" r="208"/>
    <polyline class="cycle-divider" points="-53,-199 -6,-175 -31,-122"/>
    <polyline class="cycle-divider" points="199,54 154,82 121,34"/>
    <polyline class="cycle-divider" points="-146,145 -148,93 -90,88"/>

    <g transform="rotate(200)">
      <text class="cycle-label"><textPath href="#arc-cycle-cw" startOffset="50%" text-anchor="middle">ACT</textPath></text>
    </g>
    <g transform="rotate(-36)">
      <text class="cycle-label"><textPath href="#arc-cycle-cw" startOffset="50%" text-anchor="middle">CONNECT</textPath></text>
    </g>
    <g transform="rotate(86)">
      <text class="cycle-label"><textPath href="#arc-cycle-ccw" startOffset="50%" text-anchor="middle">PERCEIVE</textPath></text>
    </g>

    <circle class="centre-disc" r="131"/>
    <circle class="centre-ring" r="123"/>
    <text class="centre-name" text-anchor="middle">
      <tspan x="0" y="-30">VEXORDA</tspan>
      <tspan x="0" y="14">LOGO</tspan>
      <tspan x="0" y="58">HERE</tspan>
    </text>
  </g>
</svg>
</body>
</html>
```